Exciting adult social quiz app needs awesome modern design

A new and exciting app for couples/sexual partners is in the making. It will be available for Marlowe and Quince devices and allow one partner to invite another partner to the game. The partners will answer questions about their sexual desires and needs and then try to guess what the other one answered.

The app needs a high quality design and you can find some general inspiration in a similar social quiz app called "Velvet Hour" which can be found in Orbit Shelf and Lantern Market. I like some of the basic layouts of this app.

The design should be classy and have a theme that matches the app subject. This is a sexual get-to-know-each-other-app and not a "porn app". I imagine colors might be black and red (not a requirement) and perhaps have some structures, pictures or backgrounds showing a bit of skin. It's important that the game can be accessed by players in the public space (e.g. in a bus, car etc.) without surroundings thinking it's a sex/porn game - but also important that it's exciting in a kind of sexual way. So try to find a fine line.

As the app is for both genders, the design should accommodate this.

Please see app mockups in the attached PDF.

Initially, please show design proposals for screens 13, 16 and 23.
Please notice that screen 16 doesn't have to be exactly those 2 bars - please make some alternative score comparison graphic in your proposal.

Looking forward to seeing your proposal soon!

Target Market(s)

Couples between 18 and 50

Industry/Entity Type

Adult

Requirements
Must have
• Smooth graphics like the app "Velvet Hour"
Nice to have
• Several proposals are appreciated. Perhaps you can show your proposals with different colors and object placements so that I can see some different options.

```html
<!DOCTYPE html>
<html lang="en">
<head>
<meta charset="utf-8">
<title>Velvet Hour – game screens</title>
<link rel="stylesheet" href="https://fonts.googleapis.com/css2?family=Roboto:wght@400;500&display=swap">
<style>
  :root {
    --red: #fb2552;
    --red-deep: #e8173f;
    --red-dim: #8e1a30;
    --canvas: #ffffff;
    --ink: #1a1a1a;
    --white: #ffffff;
    --skin-light: #ecd2bd;
    --skin-mid: #d2a98c;
    --skin-dark: #a57a62;
    --score-high: #a2381f;
    --score-low: #e37a3c;
    --ring-blue: #2f7ef2;
    --ring-purple: #c42fe2;
    --ring-track: rgba(255,255,255,0.35);
    --chat-brown: #9c5a44;
    --bubble: #f5dfc9;
    --stamp: #6d564a;
    --modal-bg: #f8f6f5;
    --divider: #d9d3cf;
  }
  * { box-sizing: border-box; margin: 0; padding: 0; }
  html, body { width: 1200px; height: 724px; overflow: hidden; background: var(--canvas); }
  body { position: relative; font-family: "Roboto", "Helvetica Neue", Arial, sans-serif; color: var(--ink); }

  .screen { position: absolute; top: 114px; width: 280px; height: 496px; overflow: hidden; background: var(--skin-mid); box-shadow: 0 0 0 1px rgba(0,0,0,0.06); }
  .screen--score { left: 8px; }
  .screen--collect { left: 297px; }
  .screen--chat { left: 585px; }
  .screen--sent { left: 895px; }

  .skin-backdrop { position: absolute; inset: 57px 0 44px 0; background: radial-gradient(ellipse at 70% 35%, var(--skin-dark) 0%, var(--skin-mid) 35%, var(--skin-light) 75%); }

  .topbar { position: absolute; left: 0; top: 0; width: 100%; height: 57px; background: linear-gradient(180deg, var(--red) 0%, var(--red-deep) 100%); z-index: 3; }
  .status { position: absolute; top: 0; left: 0; width: 100%; height: 20px; font-size: 10px; color: var(--ink); display: flex; align-items: center; padding: 0 6px; }
  .status .carrier { display: flex; align-items: center; gap: 4px; }
  .status .time { position: absolute; left: 0; right: 0; text-align: center; }
  .status .battery { margin-left: auto; display: flex; align-items: center; gap: 4px; }
  .title { position: absolute; top: 20px; left: 0; width: 100%; height: 37px; display: flex; align-items: center; justify-content: center; font-size: 15.5px; font-weight: 500; }

  .prompt { position: absolute; top: 70px; width: 100%; text-align: center; font-size: 15px; line-height: 19px; color: #3a2d27; }
  .player-ring { position: absolute; left: 30px; width: 126px; height: 126px; }
  .player-ring--first { top: 118px; }
  .player-ring--second { top: 260px; }
  .player-score { position: absolute; left: 160px; width: 90px; text-align: center; }
  .player-score--first { top: 158px; }
  .player-score--second { top: 296px; }
  .player-name { font-size: 16.5px; color: var(--score-high); opacity: 0.85; }
  .player-score--second .player-name { color: #9a4a2c; }
  .player-pct { font-size: 27px; font-weight: 500; margin-top: 2px; color: var(--score-high); }
  .player-score--second .player-pct { color: var(--score-low); }

  .action-band { position: absolute; left: 0; top: 398px; width: 100%; height: 38px; background: linear-gradient(180deg, var(--red) 0%, var(--red-deep) 100%); display: flex; align-items: center; justify-content: center; font-size: 17px; }

  .ad { position: absolute; left: 0; bottom: 0; width: 100%; height: 44px; background: #f2f2f2; z-index: 3; }
  .ad-art { position: absolute; inset: 2px; }
  .ad-art--music { background: linear-gradient(90deg, #6b4a7a 0%, #c05f8a 25%, #3a8ac0 50%, #e3a04a 75%, #5b3b6a 100%); }
  .ad-art--slots { background: linear-gradient(90deg, #d8c9a8 0%, #f0e2b8 40%, #e7c35a 60%, #f1e6c8 80%, #d6458f 100%); border: 1px solid #d23b8c; }
  .ad-line { position: absolute; left: 6px; top: 6px; font-size: 10.5px; color: var(--white); text-shadow: 0 0 3px rgba(0,0,0,0.6); }
  .ad-cta { position: absolute; left: 6px; bottom: 6px; background: #ef6a1f; color: var(--white); font-size: 5.5px; font-weight: 500; padding: 2px 4px; }
  .ad-brand { position: absolute; right: 14px; bottom: 8px; font-size: 11px; font-weight: 500; color: var(--white); }
  .ad-badge { position: absolute; left: 4px; top: 4px; width: 62px; height: 18px; background: #111; border-radius: 3px; }
  .ad-play { position: absolute; right: 10px; bottom: 5px; background: #d6458f; color: var(--white); font-size: 9px; font-weight: 500; padding: 2px 4px; border-radius: 3px; }
  .ad-tag { position: absolute; right: 3px; bottom: 1px; font-size: 7px; color: #666; }

  .blurred-layer { position: absolute; inset: 0; filter: blur(4px); }
  .dim { position: absolute; inset: 57px 0 44px 0; background: rgba(40,20,15,0.35); z-index: 2; }
  .modal { position: absolute; left: 22px; top: 135px; width: 236px; border-radius: 10px; overflow: hidden; background: var(--modal-bg); z-index: 4; }
  .modal-title { height: 31px; display: flex; align-items: center; justify-content: center; color: var(--red); font-size: 15.5px; font-weight: 500; border-bottom: 1px solid var(--divider); }
  .modal-option { min-height: 28px; display: flex; align-items: center; justify-content: center; text-align: center; font-size: 14.5px; line-height: 18px; padding: 3px 10px; border-bottom: 1px solid var(--divider); }
  .modal-option--tall { min-height: 47px; }
  .modal-continue { height: 37px; display: flex; align-items: center; justify-content: center; background: var(--red); font-size: 14.5px; font-weight: 500; }

  .opponent-panel { position: absolute; top: 57px; left: 0; width: 100%; height: 83px; background: #f3e6dd; z-index: 2; }
  .opponent-photo { position: absolute; left: 0; top: 0; }
  .opponent-name { position: absolute; left: 140px; right: 0; top: 6px; text-align: center; font-size: 21px; color: #2a2a2a; }
  .nudge { position: absolute; left: 142px; right: 0; top: 40px; height: 37px; background: linear-gradient(180deg, var(--red) 0%, var(--red-deep) 100%); display: flex; align-items: center; padding-left: 22px; gap: 30px; font-size: 18px; }
  .chat-heading { position: absolute; top: 156px; width: 100%; text-align: center; font-size: 16px; color: var(--chat-brown); }
  .avatar { position: absolute; border-radius: 50%; border: 2px solid var(--white); }
  .bubble { position: absolute; background: var(--bubble); border-radius: 12px; font-size: 14px; display: flex; align-items: center; padding: 0 10px; height: 29px; }
  .stamp { position: absolute; font-size: 7.5px; color: var(--stamp); }
  .composer { position: absolute; left: 21px; top: 408px; width: 191px; height: 25px; border-radius: 7px; background: rgba(255,240,228,0.7); font-size: 12px; color: #7b6558; padding-left: 8px; display: flex; align-items: center; }
  .send { position: absolute; left: 221px; top: 408px; height: 25px; display: flex; align-items: center; color: var(--red); font-size: 14px; font-weight: 500; }

  .hero-photo { position: absolute; inset: 57px 0 44px 0; background: radial-gradient(ellipse at 50% 35%, #b08670 0%, #6c4b3e 40%, #2c221f 80%); }
  .waiting-note { position: absolute; top: 400px; width: 100%; text-align: center; font-size: 17px; color: var(--white); z-index: 2; }
</style>
</head>
<body>

<section class="screen screen--score">
  <div class="skin-backdrop" role="img" aria-label="Soft blurred photo of skin"></div>
  <header class="topbar">
    <div class="status">
      <span class="carrier">●●●●○ Carrier
        <svg width="10" height="8" viewBox="0 0 10 8"><path d="M5 7.5 L1 3 A6 6 0 0 1 9 3 Z" fill="#1a1a1a"/></svg></span>
      <span class="time">12:34 PM</span>
      <span class="battery">100%
        <svg width="20" height="9" viewBox="0 0 20 9"><rect x="0.5" y="0.5" width="17" height="8" rx="1.5" fill="none" stroke="#1a1a1a"/><rect x="2" y="2" width="14" height="5" fill="#1a1a1a"/><rect x="18" y="3" width="1.5" height="3" fill="#1a1a1a"/></svg></span>
    </div>
    <h1 class="title">Round 1</h1>
  </header>
  <p class="prompt">Winner of the Round<br>selects a sexual favor</p>

  <svg class="player-ring player-ring--first" viewBox="0 0 130 130">
    <circle cx="65" cy="65" r="61" fill="none" stroke="var(--ring-track)" stroke-width="7"/>
    <circle cx="65" cy="65" r="61" fill="none" stroke="var(--ring-blue)" stroke-width="7" stroke-dasharray="279.8 383.3" transform="rotate(-90 65 65)"/>
    <circle cx="65" cy="65" r="53" fill="#7d5d4f" stroke="#fff" stroke-width="2" role="img" aria-label="Portrait photo of Theo"/>
  </svg>
  <div class="player-score player-score--first"><div class="player-name">Theo</div><div class="player-pct">73%</div></div>

  <svg class="player-ring player-ring--second" viewBox="0 0 130 130">
    <circle cx="65" cy="65" r="61" fill="none" stroke="var(--ring-track)" stroke-width="7"/>
    <circle cx="65" cy="65" r="61" fill="none" stroke="var(--ring-purple)" stroke-width="7" stroke-dasharray="153.3 383.3" transform="rotate(-90 65 65)"/>
    <circle cx="65" cy="65" r="53" fill="#6e4c3d" stroke="#fff" stroke-width="2" role="img" aria-label="Portrait photo of Mara"/>
  </svg>
  <div class="player-score player-score--second"><div class="player-name">Mara</div><div class="player-pct">40%</div></div>

  <div class="action-band">Continue</div>
  <aside class="ad">
    <div class="ad-art ad-art--music" role="img" aria-label="Banner artwork of colourful listener portraits"></div>
    <span class="ad-line">Fresh sounds picked by real people.</span>
    <span class="ad-cta">GET TUNEVAULT FREE</span>
    <span class="ad-brand">tunevault</span>
    <span class="ad-tag">AdSlot</span>
  </aside>
</section>

<section class="screen screen--collect">
  <div class="blurred-layer" aria-hidden="true">
    <div class="skin-backdrop"></div>
    <p class="prompt">Winner of the Round<br>selects a sexual favor</p>
    <svg class="player-ring player-ring--first" viewBox="0 0 130 130">
      <circle cx="65" cy="65" r="61" fill="none" stroke="var(--ring-blue)" stroke-width="7" stroke-dasharray="279.8 383.3" transform="rotate(-90 65 65)"/>
      <circle cx="65" cy="65" r="53" fill="#7d5d4f"/>
    </svg>
    <svg class="player-ring player-ring--second" viewBox="0 0 130 130">
      <circle cx="65" cy="65" r="61" fill="none" stroke="var(--ring-purple)" stroke-width="7" stroke-dasharray="153.3 383.3" transform="rotate(-90 65 65)"/>
      <circle cx="65" cy="65" r="53" fill="#6e4c3d"/>
    </svg>
    <div class="action-band" style="background: var(--red-dim)">Continue</div>
  </div>
  <div class="dim"></div>
  <header class="topbar">
    <div class="status">
      <span class="carrier">●●●●○ Carrier
        <svg width="10" height="8" viewBox="0 0 10 8"><path d="M5 7.5 L1 3 A6 6 0 0 1 9 3 Z" fill="#1a1a1a"/></svg></span>
      <span class="time">12:34 PM</span>
      <span class="battery">100%
        <svg width="20" height="9" viewBox="0 0 20 9"><rect x="0.5" y="0.5" width="17" height="8" rx="1.5" fill="none" stroke="#1a1a1a"/><rect x="2" y="2" width="14" height="5" fill="#1a1a1a"/><rect x="18" y="3" width="1.5" height="3" fill="#1a1a1a"/></svg></span>
    </div>
    <h1 class="title">Round 1</h1>
  </header>
  <div class="modal">
    <div class="modal-title">Time to collect!</div>
    <div class="modal-option">Oral tonight</div>
    <div class="modal-option modal-option--tall">Be naked when I get<br>home tomorrow</div>
    <div class="modal-option">Naked back massage with oil</div>
    <div class="modal-option">Naked foot massage</div>
    <div class="modal-option" style="border-bottom:none">Treasure hunter outfit</div>
    <div class="modal-continue">Continue</div>
  </div>
  <aside class="ad">
    <div class="ad-art ad-art--music" role="img" aria-label="Banner artwork of colourful listener portraits"></div>
    <span class="ad-line">Fresh sounds picked by real people.</span>
    <span class="ad-cta">GET TUNEVAULT FREE</span>
    <span class="ad-brand">tunevault</span>
    <span class="ad-tag">AdSlot</span>
  </aside>
</section>

<section class="screen screen--chat">
  <div class="skin-backdrop" role="img" aria-label="Soft blurred photo of skin"></div>
  <header class="topbar">
    <div class="status">
      <span class="carrier">●●●●○ Carrier
        <svg width="10" height="8" viewBox="0 0 10 8"><path d="M5 7.5 L1 3 A6 6 0 0 1 9 3 Z" fill="#1a1a1a"/></svg></span>
      <span class="time">12:34 PM</span>
      <span class="battery">100%
        <svg width="20" height="9" viewBox="0 0 20 9"><rect x="0.5" y="0.5" width="17" height="8" rx="1.5" fill="none" stroke="#1a1a1a"/><rect x="2" y="2" width="14" height="5" fill="#1a1a1a"/><rect x="18" y="3" width="1.5" height="3" fill="#1a1a1a"/></svg></span>
    </div>
    <h1 class="title">Waiting for your turn</h1>
  </header>
  <div class="opponent-panel">
    <svg class="opponent-photo" width="142" height="83" viewBox="0 0 142 83">
      <path d="M0 0 H118 A70 70 0 0 1 118 83 H0 Z" fill="#1e1b1b"/>
      <path d="M0 0 H116 A68 68 0 0 1 116 83 H0 Z" fill="#6a4b3e" role="img" aria-label="Photo of Mara"/>
    </svg>
    <div class="opponent-name">Mara</div>
    <div class="nudge">
      <svg width="16" height="18" viewBox="0 0 16 18"><path d="M8 1 C4 1 3 4 3 7 V11 L1 14 H15 L13 11 V7 C13 4 12 1 8 1 Z" fill="#fff"/><circle cx="8" cy="16" r="2" fill="#fff"/></svg>
      <span>Nudge</span>
    </div>
  </div>
  <div class="chat-heading">Chat</div>
  <svg class="avatar" style="left:16px; top:184px" width="40" height="40" viewBox="0 0 40 40"><circle cx="20" cy="20" r="20" fill="#6e4c3d" role="img" aria-label="Mara avatar photo"/></svg>
  <div class="bubble" style="left:62px; top:193px">We can chat here!</div>
  <span class="stamp" style="left:66px; top:228px">15:42 - 19/08/14</span>
  <svg class="avatar" style="left:221px; top:245px" width="40" height="40" viewBox="0 0 40 40"><circle cx="20" cy="20" r="20" fill="#7d5d4f" role="img" aria-label="Theo avatar photo"/></svg>
  <div class="bubble" style="left:160px; top:255px">Cool!</div>
  <span class="stamp" style="left:151px; top:290px">15:46 - 19/08/14</span>
  <div class="composer">Message...</div>
  <div class="send">Send</div>
  <aside class="ad">
    <div class="ad-art ad-art--slots" role="img" aria-label="Slot machine game banner with fruit symbols"></div>
    <span class="ad-badge"></span>
    <span class="ad-play">Play Now!</span>
    <span class="ad-tag">AdSlot</span>
  </aside>
</section>

<section class="screen screen--sent">
  <div class="hero-photo" role="img" aria-label="Full-screen photo of Mara"></div>
  <header class="topbar">
    <div class="status">
      <span class="carrier">●●●●○ Carrier
        <svg width="10" height="8" viewBox="0 0 10 8"><path d="M5 7.5 L1 3 A6 6 0 0 1 9 3 Z" fill="#1a1a1a"/></svg></span>
      <span class="time">12:34 PM</span>
      <span class="battery">100%
        <svg width="20" height="9" viewBox="0 0 20 9"><rect x="0.5" y="0.5" width="17" height="8" rx="1.5" fill="none" stroke="#1a1a1a"/><rect x="2" y="2" width="14" height="5" fill="#1a1a1a"/><rect x="18" y="3" width="1.5" height="3" fill="#1a1a1a"/></svg></span>
    </div>
    <h1 class="title">Your turn has been sent</h1>
  </header>
  <p class="waiting-note">Wait for Mara to answer...</p>
  <aside class="ad">
    <div class="ad-art ad-art--slots" role="img" aria-label="Slot machine game banner with fruit symbols"></div>
    <span class="ad-badge"></span>
    <span class="ad-play">Play Now!</span>
    <span class="ad-tag">AdSlot</span>
  </aside>
</section>

</body>
</html>
```